whitening syringe artwork design

3ml syringe with silkscreen printing:
sample:
https://www.quorvashop.example/Velvo-Crane-Whitening-Syringes-Carbamide/dp/Q51842KX93/ref=sr_1_6?crid=7ZP42WQ81LMRT&dchild=1&keywords=whitening+syringes&qid=1698802214&sprefix=whitening+sy%2Caps%2C150&sr=8-6
inside the writing:
"teeth whitening gel " change to "Orvanne WHITENING GEL"
"Advanced formula" change to our logo and "Not all gels are created equal. "

additional requirements:
Inches: 2.01" wide x 1.34" around

CM: 5.1cm wide x 3.4cm around

See attached template: Generic_Syringe Labels 3ml_Silkscreen.pdf

- Leave the volume gage where it is, so it prints correctly on the syringe

- Feel free to change the color and font style

- An "identifying marker" is required: Teeth Whitening Syringe or Teeth Whitening Gel (for example)

- Replace "Teeth Whitening Gel - Advanced Formula" with your text and logo - it is there as a placeholder

-We require PDF files created to print ready specifications. Color images should be down-sampled to 300DPI

-Please provide us your Tintora color references for the color used in your artwork

https://www.tintora.example/color-finder#/pick?tintoraBook=tintoraSolidCoatedV3M2

-Please ensure that all fonts are embedded in the PDF document or make sure you convert fonts to outlines to prevent any issues with fonts (AI-Type-Create Outlines)

We will need your print ready artwork in a high resolution PDF file

teeth whitening ecommerce

• follow the guide document, and add text I want, color code from Tintora is provided

```html
<!DOCTYPE html>
<html lang="en">
<head>
<meta charset="utf-8">
<title>Orvanne Whitening Gel – Syringe Artwork</title>
<link rel="stylesheet" href="https://fonts.googleapis.com/css2?family=Montserrat:ital,wght@0,400;0,500;0,600;0,700;1,400&family=Merriweather:ital,wght@1,400&display=swap">
<style>
  :root{
    --blue-312:#00a9c8;
    --black-3:#2b2d28;
    --coral-169:#f9b8ae;
    --teal-3252:#55d3c9;
    --tag-teal:#6ae3d9;
    --sky-top:#8ef6fd;
    --sky-bottom:#6fd2f0;
    --ink:#2a2a2a;
    --label-white:#fcfcfc;
    --paper:#ffffff;
  }
  *{margin:0;padding:0;box-sizing:border-box}
  html,body{width:800px;height:1200px;overflow:hidden;background:var(--paper)}
  .sheet{position:relative;width:800px;height:1200px;font-family:"Montserrat",sans-serif;color:var(--ink)}
  .hero{position:absolute;left:0;top:0;width:800px;height:760px;
    background:linear-gradient(200deg,var(--sky-top) 0%,#84e6fb 45%,var(--sky-bottom) 100%)}
  .hero-art{position:absolute;left:0;top:0;width:800px;height:760px}
  .hero-brand{position:absolute;left:582px;top:700px;display:flex;align-items:center;gap:12px;
    font-family:"Montserrat",sans-serif;font-weight:700;font-size:32px;letter-spacing:3px;color:var(--paper)}
  .brand-dot{width:34px;height:34px;border-radius:50%;background:var(--paper)}
  .section-title{position:absolute;left:0;width:800px;top:768px;text-align:center;font-weight:500;font-size:31px;color:var(--ink)}
  .artwork{position:absolute;left:0;top:0;width:800px;height:1200px}

  .label-bg{fill:var(--label-white)}
  .coral{fill:var(--coral-169)}
  .rule-blue{stroke:var(--blue-312);stroke-width:1}
  .dim-line{stroke:var(--ink);stroke-width:1.4;fill:none}
  .dim-label{font-family:"Montserrat",sans-serif;font-size:16px;fill:var(--ink)}
  .gauge-tick{stroke:var(--ink);stroke-width:1.2}
  .gauge-num{font-family:"Montserrat",sans-serif;font-weight:700;font-size:10px;fill:var(--ink)}
  .gauge-unit{font-family:"Montserrat",sans-serif;font-size:7px;fill:var(--ink)}
  .product-name{font-family:"Merriweather",serif;font-style:italic;font-size:15.5px;fill:var(--blue-312)}
  .tagline{font-family:"Montserrat",sans-serif;font-style:italic;font-size:7.6px;fill:var(--ink)}
  .mini-brand{font-family:"Montserrat",sans-serif;font-weight:600;font-size:7px;letter-spacing:.6px;fill:var(--ink)}
  .tag-body{fill:var(--tag-teal)}
  .tag-title{font-family:"Montserrat",sans-serif;font-weight:700;font-size:11.5px;fill:var(--black-3)}
  .tag-volume{font-family:"Montserrat",sans-serif;font-size:9px;fill:var(--black-3)}
  .tag-brand{font-family:"Montserrat",sans-serif;font-weight:600;font-size:4.5px;fill:var(--black-3)}
  .palette-title{font-family:"Montserrat",sans-serif;font-weight:500;font-size:17px;fill:var(--ink)}
  .swatch-code{font-family:"Montserrat",sans-serif;font-size:13px;fill:var(--ink)}
  .sw-blue{fill:var(--blue-312)}
  .sw-black{fill:var(--black-3)}
  .sw-coral{fill:var(--coral-169)}
  .sw-teal{fill:var(--teal-3252)}
  .footer-brand{font-family:"Montserrat",sans-serif;font-weight:700;font-size:34px;letter-spacing:3px;fill:var(--black-3)}
</style>
</head>
<body>
<div class="sheet">
  <div class="hero"></div>

  <svg class="hero-art" viewBox="0 0 800 760" xmlns="http://www.w3.org/2000/svg">
    <defs>
      <symbol id="barrel-art" viewBox="0 0 205 137">
        <rect class="label-bg" x="0" y="0" width="205" height="137"/>
        <circle class="coral" cx="83" cy="16" r="3.5"/>
        <text class="mini-brand" x="89" y="19">GLIMMO</text>
        <text class="product-name" x="14" y="39">Orvanne WHITENING GEL</text>
        <line class="rule-blue" x1="14" y1="45.5" x2="75" y2="45.5"/>
        <text class="tagline" x="78" y="48">Not all gels are created equal</text>
        <line class="gauge-tick" x1="12" y1="78" x2="12" y2="116"/>
        <line class="gauge-tick" x1="43" y1="78" x2="43" y2="116"/>
        <line class="gauge-tick" x1="73" y1="78" x2="73" y2="116"/>
        <line class="gauge-tick" x1="108" y1="78" x2="108" y2="116"/>
        <line class="gauge-tick" x1="143" y1="78" x2="143" y2="116"/>
        <line class="gauge-tick" x1="173" y1="78" x2="173" y2="106"/>
        <line class="gauge-tick" x1="204" y1="78" x2="204" y2="116"/>
        <text class="gauge-unit" transform="translate(4 80) rotate(90)">ml/cc</text>
        <text class="gauge-num" transform="translate(8 121) rotate(90)">3</text>
        <text class="gauge-num" transform="translate(39 118) rotate(90)">2½</text>
        <text class="gauge-num" transform="translate(69 121) rotate(90)">2</text>
        <text class="gauge-num" transform="translate(104 118) rotate(90)">1½</text>
        <text class="gauge-num" transform="translate(139 121) rotate(90)">1</text>
        <text class="gauge-num" transform="translate(169 120) rotate(90)">½</text>
      </symbol>
      <symbol id="tag-art" viewBox="0 0 347 99">
        <rect class="tag-body" x="145" y="8" width="202" height="33" rx="3"/>
        <rect class="tag-body" x="0" y="0" width="150" height="49" rx="8"/>
        <rect class="tag-body" x="0" y="50" width="150" height="49" rx="8"/>
        <text class="tag-title" x="75" y="19" text-anchor="middle">Teeth Whitening Gel</text>
        <text class="tag-volume" x="75" y="30" text-anchor="middle">3 ml</text>
        <circle class="coral" cx="64" cy="38" r="2"/>
        <text class="tag-brand" x="67" y="40">GLIMMO</text>
        <g transform="rotate(180 75 74.5)">
          <text class="tag-title" x="75" y="68" text-anchor="middle">Teeth Whitening Gel</text>
          <text class="tag-volume" x="75" y="79" text-anchor="middle">3 ml</text>
          <circle class="coral" cx="64" cy="87" r="2"/>
          <text class="tag-brand" x="67" y="89">GLIMMO</text>
        </g>
      </symbol>
    </defs>
    <use href="#barrel-art" x="205" y="90" width="390" height="261"/>
    <use href="#tag-art" x="122" y="420" width="555" height="158"/>
  </svg>

  <div class="hero-brand"><span class="brand-dot"></span>GLIMMO</div>

  <h1 class="section-title">Design</h1>

  <svg class="artwork" viewBox="0 0 800 1200" xmlns="http://www.w3.org/2000/svg">
    <use href="#barrel-art" x="113" y="832" width="205" height="137"/>

    <path class="dim-line" d="M80 832H92M86 832V969M80 969H92"/>
    <text class="dim-label" x="48" y="904">3.4</text>
    <path class="dim-line" d="M113 981V993M113 987H318M318 981V993"/>
    <text class="dim-label" x="200" y="1009">5.1</text>

    <use href="#tag-art" x="99" y="1023" width="347" height="99"/>

    <path class="dim-line" d="M80 1023H92M86 1023V1072M80 1072H92"/>
    <text class="dim-label" x="44" y="1054">1.27</text>
    <path class="dim-line" d="M462 1031H474M468 1031V1064M462 1064H474"/>
    <text class="dim-label" x="481" y="1054">0.85</text>
    <path class="dim-line" d="M249 1079V1091M249 1085H446M446 1079V1091"/>
    <text class="dim-label" x="329" y="1108">6.35</text>
    <path class="dim-line" d="M99 1140V1152M99 1146H249M249 1140V1152"/>
    <text class="dim-label" x="160" y="1169">3.81</text>

    <text class="palette-title" x="606" y="863" text-anchor="middle">Tintora</text>
    <rect class="sw-blue" x="464" y="883" width="54" height="54" rx="6"/>
    <rect class="sw-black" x="539" y="883" width="54" height="54" rx="6"/>
    <rect class="sw-coral" x="617" y="883" width="54" height="54" rx="6"/>
    <rect class="sw-teal" x="695" y="883" width="54" height="54" rx="6"/>
    <text class="swatch-code" x="491" y="959" text-anchor="middle">312 c</text>
    <text class="swatch-code" x="566" y="959" text-anchor="middle">Black 3 c</text>
    <text class="swatch-code" x="644" y="959" text-anchor="middle">169 c</text>
    <text class="swatch-code" x="722" y="959" text-anchor="middle">3252 c</text>

    <circle class="coral" cx="592" cy="1141" r="18"/>
    <text class="footer-brand" x="620" y="1154">GLIMMO</text>
  </svg>
</div>
</body>
</html>
```